Ashbrook Pit Advertising / Price List

Create a 1 page document for print and email showcasing what we have available in our Quarry. Bottom of sample should have the information included and then the rest of the document focus on items and services available with the quarry. The top section will need room to list about items below and have about 5 pictures that I am working on getting.

Materials Available for Pick Up and/or Delivery:
Recycled Breaker Run
3/4" & 1 1/4" Crushed Recycled Asphalt
1 1/4" Crushed Recycled Stone
1 1/4" Screened "Dig Right On In"
3/4" Clean Stone
3/8" Washed Pea Stone
Mound Sand
Fill Sand Material
Fill/Clay Fill Material
Compost
Peot Moss
Topsoil
Reclaimed Cream City Bricks

Dumping of Materials with Approval:
Clean Concrete
Dirty and / or Large Concrete or Tolvaran
Clean Brick
Asphalt
Fill Material
Brush and / or Stumps
Hydro Vac Slurry Dumping

Target Market(s)

Contractors in our area

Industry/Entity Type

Trucking & Excavation

Colors
EB3D1F
EC4F4E
F09395
F8D3D4
FCEDEE

Requirements
Must have
• Similar Look & Feel as Sample Copy

```html
<!DOCTYPE html>
<html lang="en">
<head>
<meta charset="utf-8">
<title>Ashbrook Pit – Materials &amp; Services</title>
<link href="https://fonts.googleapis.com/css2?family=Roboto:wght@400;500;700&family=Rubik:wght@600&display=swap" rel="stylesheet">
<style>
  :root{
    --red:#E41E26;
    --red-deep:#EB3D1F;
    --red-soft:#EC4F4E;
    --rose:#F09395;
    --blush:#F8D3D4;
    --mist:#FCEDEE;
    --ink:#1d1d1d;
    --white:#ffffff;
  }
  *{margin:0;padding:0;box-sizing:border-box}
  html,body{width:848px;height:1200px;overflow:hidden;background:#ffffff}
  .flyer{position:relative;width:848px;height:1200px;background:var(--blush);overflow:hidden;font-family:"Roboto",Arial,sans-serif;color:var(--ink)}
  .backdrop{position:absolute;inset:0;width:848px;height:1200px}
  .brand{position:absolute;left:22px;top:60px;color:var(--white);display:flex;align-items:center;gap:8px}
  .brand-dot{width:12px;height:12px;border-radius:50%;background:var(--white);flex:none}
  .brand-name{font-weight:700;font-size:34px;line-height:1;letter-spacing:-0.3px}
  .brand-tag{position:absolute;left:22px;top:102px;color:var(--white);font-weight:700;font-size:6.5px;letter-spacing:.2px}
  .brand-place{position:absolute;left:92px;top:112px;color:var(--white);font-weight:700;font-size:8px;letter-spacing:.3px;text-align:center;line-height:10px}
  .section-title{position:absolute;left:349px;font-weight:500;font-size:17.5px;color:var(--ink);white-space:nowrap;letter-spacing:-0.1px}
  .list{position:absolute;list-style:none;font-size:11.3px;line-height:14.5px;color:var(--ink)}
  .list li{position:relative;padding-left:7px}
  .list li::before{content:"";position:absolute;left:0;top:5px;width:3.5px;height:3.5px;border-radius:50%;background:var(--red)}
  .list.dump{font-size:10.3px;line-height:13.6px}
  .divider{position:absolute;top:246px;width:1px;height:93px;background:var(--red)}
  .service-photo{position:absolute;top:904px;width:158px;height:158px;border-radius:50%;border:5px solid var(--white)}
  .services-title{position:absolute;left:0;width:848px;top:1072px;text-align:center;font-weight:700;font-size:21px;color:var(--blush)}
  .service{position:absolute;top:1104px;width:200px;text-align:center;font-weight:700;font-size:18.5px;line-height:19px;color:var(--blush)}
  .contact-bar{position:absolute;left:0;top:1158px;width:848px;height:42px;background:var(--rose)}
  .contact{position:absolute;top:6px;display:flex;align-items:center;gap:6px;font-family:"Rubik",Arial,sans-serif;font-weight:600;font-size:13.4px;line-height:14px;color:var(--ink)}
  .contact svg{flex:none}
</style>
</head>
<body>
<main class="flyer">
  <svg class="backdrop" viewBox="0 0 848 1200" aria-hidden="true">
    <defs>
      <linearGradient id="yardTone" x1="0" y1="0" x2="0" y2="1">
        <stop offset="0" stop-color="#a9c8e6"/>
        <stop offset=".2" stop-color="#a9a297"/>
        <stop offset=".5" stop-color="#d99690"/>
        <stop offset=".8" stop-color="#cbc4bb"/>
        <stop offset="1" stop-color="#c9c3bb"/>
      </linearGradient>
    </defs>
    <path d="M0 0 H320 C290 90 200 180 0 199 Z" fill="var(--red)"/>
    <path d="M0 412 C70 470 240 470 312 410 C250 470 80 490 0 452 Z" fill="var(--red)"/>
    <path d="M300 450 C420 400 520 352 610 352 C700 352 790 375 848 395 L848 470 L300 470 Z" fill="var(--red)"/>
    <path d="M0 495 C150 470 300 420 470 400 C600 385 740 380 848 448 L848 1000 L0 1000 Z" fill="url(#yardTone)" role="img" aria-label="Photo of red roll-off dumpsters and trucks parked at the quarry yard beside a river"/>
    <path d="M0 890 C180 990 380 900 470 860 C600 800 760 800 848 890 L848 1200 L0 1200 Z" fill="var(--white)"/>
    <path d="M0 1000 C220 1010 360 900 480 860 C620 815 760 840 848 925 L848 1200 L0 1200 Z" fill="var(--red)"/>
    <path d="M400 1000 C470 930 560 880 650 870 C730 862 800 880 848 900 L848 880 C780 845 700 838 620 850 C530 865 450 920 400 1000 Z" fill="var(--white)"/>
  </svg>

  <div class="brand"><span class="brand-dot"></span><span class="brand-name">Ashbrook Pit</span></div>
  <div class="brand-tag">CRUSHING . EXCAVATING . SNOW REMOVAL . TRUCKING</div>
  <div class="brand-place">QUARRY &amp; HAULING<br>FENWICK, WI</div>

  <h2 class="section-title" style="top:111px;display:none"></h2>
  <h2 class="section-title" style="top:13px">Materials Available for Pick Up and/or Delivery:</h2>
  <ul class="list" style="left:338px;top:52px;width:180px">
    <li>Recycled Breaker Run</li>
    <li>3/4" &amp; 1 1/4" Crushed<br>Recycled Asphalt</li>
    <li>1 1/4" Crushed Recycled Stone</li>
    <li>1 1/4" Screened "Dig Right<br>On In"</li>
  </ul>
  <ul class="list" style="left:510px;top:52px;width:170px">
    <li style="padding-left:12px">3/4" Clean Stone</li>
    <li style="padding-left:12px">3/8" Washed Pea Stone</li>
    <li style="padding-left:12px">Mound Sand</li>
    <li style="padding-left:12px">Fill Sand Material</li>
    <li style="padding-left:12px">Fill/Clay Fill Material</li>
  </ul>
  <ul class="list" style="left:711px;top:52px;width:130px">
    <li>Compost</li>
    <li>Peot Moss</li>
    <li>Topsoil</li>
    <li>Reclaimed Cream<br>City Bricks</li>
  </ul>

  <h2 class="section-title" style="top:137px">Dumping of Materials with Approval:</h2>
  <ul class="list dump" style="left:338px;top:175px;width:180px">
    <li>Clean Concrete</li>
    <li>Dirty and / or Large Concrete<br>or Tolvaran</li>
  </ul>
  <ul class="list dump" style="left:516px;top:175px;width:160px">
    <li>Clean Brick</li>
    <li>Asphalt</li>
    <li>Fill Material</li>
  </ul>
  <ul class="list dump" style="left:710px;top:175px;width:135px">
    <li style="padding-left:9px">Brush and / or Stumps</li>
    <li style="padding-left:9px">Hydro Vac Slurry</li>
    <li style="padding-left:9px">Dumping</li>
  </ul>

  <span class="divider" style="left:154px"></span>
  <span class="divider" style="left:333px"></span>
  <span class="divider" style="left:489px"></span>
  <span class="divider" style="left:665px"></span>

  <div class="service-photo" style="left:47px;background:linear-gradient(160deg,#8a7868,#c8ad6a 55%,#a59a90)" role="img" aria-label="Photo of an excavator demolishing a brick building"></div>
  <div class="service-photo" style="left:249px;background:linear-gradient(180deg,#9cc0e8 0%,#b7d0ee 45%,#9c7660 70%,#8a6a56)" role="img" aria-label="Photo of an excavator digging soil on a job site"></div>
  <div class="service-photo" style="left:452px;background:linear-gradient(180deg,#c6c9cf 0%,#b1aea7 45%,#f4f4f6 65%,#ffffff)" role="img" aria-label="Photo of loaders clearing snow from a parking lot"></div>
  <div class="service-photo" style="left:652px;background:linear-gradient(170deg,#dcdcdc,#a89c8f 55%,#8b7d70)" role="img" aria-label="Photo of an excavator clearing debris inside a building"></div>

  <h2 class="services-title">Our Commercial and Residential Services Include</h2>
  <div class="service" style="left:24px">Brush Cutting</div>
  <div class="service" style="left:228px;top:1106px">Excavating</div>
  <div class="service" style="left:416px;width:240px">Snow Plowing and<br>Removal</div>
  <div class="service" style="left:631px">Trucking</div>

  <footer class="contact-bar">
    <div class="contact" style="left:36px">
      <svg width="13" height="17" viewBox="0 0 12 16"><path d="M6 0C2.7 0 0 2.6 0 5.9 0 10.3 6 16 6 16s6-5.7 6-10.1C12 2.6 9.3 0 6 0Zm0 8.3A2.4 2.4 0 1 1 6 3.5a2.4 2.4 0 0 1 0 4.8Z" fill="var(--ink)"/></svg>
      <span>1480 Marlow Road<br>Fenwick, WI 54999</span>
    </div>
    <div class="contact" style="left:259px">
      <svg width="13" height="28" viewBox="0 0 13 28"><rect x="1" y="2" width="11" height="8" fill="var(--ink)"/><path d="M1 2l5.5 4.5L12 2" stroke="var(--rose)" stroke-width="1.2" fill="none"/><circle cx="6.5" cy="20" r="5" fill="none" stroke="var(--ink)" stroke-width="1.1"/><ellipse cx="6.5" cy="20" rx="2.2" ry="5" fill="none" stroke="var(--ink)" stroke-width="1"/><path d="M1.5 20h10" stroke="var(--ink)" stroke-width="1"/></svg>
      <span>dispatch@ashbrookpit.example<br>www.ashbrookpit.example</span>
    </div>
    <div class="contact" style="left:556px">
      <svg width="16" height="18" viewBox="0 0 16 18"><path d="M3.4 0.5l2.6 3.8-1.6 2.1c.9 2.5 2.6 4.6 5 6.1l2.1-1.4 3.8 2.8-1.5 3.3C8 17.3 0.8 9.8 0.5 2.2Z" fill="var(--ink)"/></svg>
      <span style="margin-left:8px">Call or Text 920-555-0147<br>Fax 920-555-0148</span>
    </div>
  </footer>
</main>
</body>
</html>
```